Seeking funky, innovative business cards

I am looking to refresh our current business cards to something more engaging, visual and impactful. We are a management consultancy firm, see website (www.larkstone-partners.com.au). I've included our colour scheme, sample of the slides we use and our old business cards. We would like our cards to have icons. The card should display:- Name- Title- Mobile number- Address- Email address- Website - Company logo- Our purpose statement "we shape the brightest rooms anywhere to thrive"

Contact Information for Business Card

Brennan Ulfsson
Consultant
0468 927 341
Level 5, 218 Wexley Street, Brambleton 3921
brennan@larkstone-partners.com.au
www.larkstone-partners.com.au

Purpose statement "we shape the brightest rooms anywhere to thrive"
LOGO available in google images

Font styles to use
Other font styles liked:
• Open Sans Light, Bebas Neue (open to other cool foints)

Colors
ffc214
5c5c5c
f5f5f5
fefefe

Requirements
Must have
• - Name
• - Title
• - Mobile number
• - Address
• - Email address
• - Website
• - Company logo
• - Our purpose statement "we shape the brightest rooms anywhere to thrive"
Nice to have
• - Icons
• - Colour (see our colour scheme"

```html
<!DOCTYPE html>
<html lang="en">
<head>
<meta charset="utf-8">
<title>Larkstone Partners — Business Card</title>
<link rel="stylesheet" href="https://fonts.googleapis.com/css2?family=Open+Sans:ital,wght@0,300;0,400;0,600;1,600&display=swap">
<style>
  :root {
    --brand-yellow: #ffc214;
    --brand-grey: #5c5c5c;
    --card-dark: #4a4d4f;
    --card-dark-deep: #3a3c3e;
    --card-light: #fefefe;
    --card-light-shade: #f5f5f5;
    --text-grey: #55585a;
    --rule-grey: #d6d6d6;
    --backdrop: #e7e4df;
  }
  * { box-sizing: border-box; margin: 0; padding: 0; }
  html, body {
    width: 1200px; height: 780px; overflow: hidden;
    background: var(--backdrop);
    font-family: "Open Sans", Arial, sans-serif;
  }
  .stage {
    position: relative; width: 1200px; height: 780px;
    display: flex; align-items: center; justify-content: center; gap: 60px;
  }
  .card {
    position: relative; width: 520px; height: 310px;
    border-radius: 22px; overflow: hidden;
    box-shadow: 0 10px 24px rgba(0,0,0,.18);
  }

  /* ---------- Front ---------- */
  .card-front { background: var(--card-dark); }
  .card-front .sweep { position: absolute; inset: 0; }
  .holder { position: absolute; top: 14px; right: 30px; text-align: right; }
  .holder-name { color: #fff; font-size: 21px; font-weight: 400; letter-spacing: .2px; }
  .holder-title { color: var(--brand-yellow); font-size: 14px; font-weight: 400; margin-top: -2px; }

  .brand { position: absolute; display: flex; align-items: center; gap: 12px; }
  .brand-dot { width: 14px; height: 14px; border-radius: 50%; background: var(--brand-yellow); flex: none; }
  .brand-name { font-weight: 300; line-height: 1; }
  .brand-name .word { display: block; }
  .brand-name .sub { display: block; letter-spacing: 4px; }

  .card-front .brand { left: 32px; top: 138px; }
  .card-front .brand-name { color: var(--brand-grey); }
  .card-front .brand-name .word { font-size: 50px; }
  .card-front .brand-name .sub { font-size: 12px; margin-top: 4px; padding-left: 3px; }

  .contacts { position: absolute; left: 34px; bottom: 22px; list-style: none; }
  .contacts li { display: flex; align-items: center; gap: 9px; color: var(--text-grey); font-size: 12.5px; line-height: 21px; }
  .contacts svg { width: 13px; height: 13px; flex: none; }

  .divider { position: absolute; left: 338px; top: 150px; width: 1px; height: 130px; background: var(--rule-grey); }
  .address { position: absolute; left: 356px; bottom: 30px; color: var(--text-grey); font-size: 12.5px; line-height: 19px; font-style: normal; }

  /* ---------- Back ---------- */
  .card-back { background: radial-gradient(ellipse at 40% 30%, #55595b 0%, var(--card-dark) 55%, var(--card-dark-deep) 100%); }
  .card-back .brand { left: 50%; top: 86px; transform: translateX(-50%); }
  .card-back .brand-name { color: #fff; }
  .card-back .brand-name .word { font-size: 58px; }
  .card-back .brand-name .sub { font-size: 13px; margin-top: 6px; padding-left: 4px; }
  .purpose {
    position: absolute; left: 0; right: 0; top: 212px; text-align: center;
    color: var(--card-light-shade); font-size: 15px; font-weight: 600; font-style: italic;
  }
</style>
</head>
<body>
<main class="stage">

  <section class="card card-front" aria-label="Business card front">
    <svg class="sweep" viewBox="0 0 520 310" preserveAspectRatio="none" aria-hidden="true">
      <defs>
        <linearGradient id="paper" x1="0" y1="0" x2="0" y2="1">
          <stop offset="0" stop-color="#fefefe"/>
          <stop offset="1" stop-color="#f5f5f5"/>
        </linearGradient>
      </defs>
      <path d="M0,310 L0,132 Q250,62 520,76 L520,310 Z" fill="url(#paper)"/>
      <path d="M0,126 Q250,56 520,70" fill="none" stroke="#ffc214" stroke-width="6"/>
    </svg>

    <div class="holder">
      <p class="holder-name">Brennan Ulfsson</p>
      <p class="holder-title">Consultant</p>
    </div>

    <div class="brand">
      <span class="brand-dot"></span>
      <p class="brand-name"><span class="word">Larkstone</span><span class="sub">PARTNERS</span></p>
    </div>

    <ul class="contacts">
      <li>
        <svg viewBox="0 0 14 14" aria-hidden="true"><rect x="3" y="1" width="8" height="12" rx="1.5" fill="none" stroke="#ffc214" stroke-width="1.6"/><circle cx="7" cy="10.6" r=".9" fill="#ffc214"/></svg>
        0468 927 341
      </li>
      <li>
        <svg viewBox="0 0 14 14" aria-hidden="true"><rect x="1" y="3" width="12" height="8.5" rx="1" fill="#ffc214"/><path d="M1.5,3.6 L7,8 L12.5,3.6" fill="none" stroke="#fff" stroke-width="1.2"/></svg>
        brennan@larkstone-partners.com.au
      </li>
      <li>
        <svg viewBox="0 0 14 14" aria-hidden="true"><circle cx="7" cy="7" r="6" fill="#ffc214"/><path d="M1,7 H13 M7,1 C4,4 4,10 7,13 M7,1 C10,4 10,10 7,13" fill="none" stroke="#fff" stroke-width="1"/></svg>
        www.larkstone-partners.com.au
      </li>
    </ul>

    <span class="divider" aria-hidden="true"></span>

    <address class="address">Level 5, 218 Wexley Street<br>Brambleton 3921</address>
  </section>

  <section class="card card-back" aria-label="Business card back">
    <div class="brand">
      <span class="brand-dot"></span>
      <p class="brand-name"><span class="word">Larkstone</span><span class="sub">PARTNERS</span></p>
    </div>
    <p class="purpose">we shape the brightest rooms anywhere to thrive</p>
  </section>

</main>
</body>
</html>
```